Business Card design for law firm = Brightvale Australia

We are seeking a new design for our business cards.
We are keeping our logo, which is attached.
We need space for
Name
Title
Address is , which is
Level 7
214 Marlowe Street
Sydney NSW 2047
Phone :
Mobile :
Fax :
Email :
DX :
website www.brightvale-example.com.au

Industry/Entity Type

Law Firm / Banking and Finance

Contact Information for Business Card

We are seeking a new design for our business cards. We are keeping our logo. We need space for Name Title Address is Level 7 214 Marlowe Street Sydney NSW 2047 Phone Mobile Fax Email DX website www.brightvale-example.com.au

Colors
0054AA
0677BA
7BADD7
CADEEF
E8F1F8

Requirements
Must have
• see our website for general feel www.brightvale-example.com.au

```html
<!DOCTYPE html>
<html lang="en">
<head>
<meta charset="utf-8">
<title>Brightvale Business Card</title>
<link rel="stylesheet" href="https://fonts.googleapis.com/css2?family=Tinos:wght@400;700&family=Roboto:wght@400&family=Open+Sans:wght@400&display=swap">
<style>
  :root {
    --brand-blue: #2160b0;
    --brand-deep: #0054aa;
    --brand-mid: #0677ba;
    --brand-light: #7badd7;
    --ink: #2b2b2b;
    --paper: #ffffff;
    --backdrop: #2a2b2d;
  }
  * { box-sizing: border-box; margin: 0; padding: 0; }
  html, body { width: 1200px; height: 900px; overflow: hidden; }
  body {
    background: var(--backdrop);
    display: flex;
    flex-direction: column;
    align-items: center;
    justify-content: center;
    gap: 44px;
    font-family: "Roboto", Arial, sans-serif;
  }
  .card {
    position: relative;
    width: 620px;
    height: 360px;
    border-radius: 22px;
    overflow: hidden;
    box-shadow: 0 10px 30px rgba(0,0,0,0.45);
  }

  /* Front */
  .card-front {
    background: var(--brand-blue);
    display: flex;
    flex-direction: column;
    align-items: center;
    justify-content: center;
    color: var(--paper);
  }
  .wordmark {
    font-family: "Tinos", "Times New Roman", serif;
    font-weight: 400;
    line-height: 1;
  }
  .card-front .wordmark { font-size: 74px; letter-spacing: 1px; }
  .tagline {
    font-family: "Open Sans", Arial, sans-serif;
    letter-spacing: 3px;
  }
  .card-front .tagline { font-size: 21px; margin-top: 10px; }

  /* Back */
  .card-back { background: var(--paper); color: var(--ink); }
  .holder {
    position: absolute;
    left: 46px;
    top: 78px;
  }
  .holder-name {
    font-family: "Tinos", "Times New Roman", serif;
    font-weight: 700;
    font-size: 25px;
    color: var(--brand-deep);
    letter-spacing: 0.5px;
  }
  .holder-title { font-size: 15px; margin-top: 2px; }
  .rule {
    position: absolute;
    left: 40px;
    right: 40px;
    top: 168px;
    height: 1px;
    background: var(--brand-mid);
  }
  .contacts {
    position: absolute;
    left: 46px;
    top: 182px;
    list-style: none;
    font-size: 15.5px;
    line-height: 23px;
  }
  .contacts li { display: flex; align-items: center; gap: 8px; }
  .contacts svg { width: 13px; height: 13px; fill: var(--brand-mid); flex: none; }
  .back-brand {
    position: absolute;
    right: 46px;
    top: 64px;
    text-align: right;
  }
  .back-brand .wordmark { font-size: 54px; color: var(--brand-deep); }
  .back-brand .tagline { font-size: 14px; color: var(--brand-mid); margin-top: 8px; letter-spacing: 2.4px; }
  .address {
    position: absolute;
    right: 46px;
    top: 186px;
    text-align: right;
    font-size: 16px;
    line-height: 22px;
  }
  .wave { position: absolute; left: 0; bottom: 0; width: 620px; height: 110px; }
  .website {
    position: absolute;
    right: 40px;
    bottom: 14px;
    color: var(--paper);
    font-size: 16px;
    letter-spacing: 0.3px;
  }
</style>
</head>
<body>
  <section class="card card-front">
    <div class="wordmark">Brightvale</div>
    <div class="tagline">strategic legal outsourcing</div>
  </section>

  <section class="card card-back">
    <div class="holder">
      <div class="holder-name">MARA ELLISON</div>
      <div class="holder-title">Chief Legal Officer, BA, LLB (Hons)</div>
    </div>

    <div class="back-brand">
      <div class="wordmark">Brightvale</div>
      <div class="tagline">strategic legal outsourcing</div>
    </div>

    <div class="rule"></div>

    <ul class="contacts">
      <li><svg viewBox="0 0 16 16"><path d="M3.5 1l3 3-1.6 1.8c.8 1.9 2.4 3.5 4.3 4.3L11 8.5l3 3-2 2.5C6 13.5 2.5 10 1 4z"/></svg>02 9000 0141</li>
      <li><svg viewBox="0 0 16 16"><path d="M4 0h8a1 1 0 0 1 1 1v14a1 1 0 0 1-1 1H4a1 1 0 0 1-1-1V1a1 1 0 0 1 1-1zm1 2v10h6V2zm3 11a1 1 0 1 0 0 2 1 1 0 0 0 0-2z"/></svg>02 9000 0287</li>
      <li><svg viewBox="0 0 16 16"><path d="M4 0h8v4H4zM1 5h14a1 1 0 0 1 1 1v6h-3v4H3v-4H0V6a1 1 0 0 1 1-1zm4 6v3h6v-3z"/></svg>02 9000 0356</li>
      <li><svg viewBox="0 0 16 16"><path d="M0 3h16v10H0zm1.5 1.2L8 9l6.5-4.8V4h-13z"/></svg>mara.ellison@brightvale-example.com.au</li>
    </ul>

    <div class="address">
      Level 7, 214 Marlowe Street<br>
      Sydney NSW 2047
    </div>

    <svg class="wave" viewBox="0 0 620 110" preserveAspectRatio="none" aria-hidden="true">
      <path d="M220,110 C360,78 500,58 620,52 L620,110 Z" fill="var(--brand-blue)"/>
      <path d="M320,58 C440,56 540,66 620,80 L620,72 C540,58 440,50 320,58 Z" fill="var(--brand-mid)"/>
      <path d="M300,62 C430,60 540,72 620,92 L620,86 C540,68 430,56 300,62 Z" fill="var(--paper)"/>
    </svg>
    <div class="website">www.brightvale-example.com.au</div>
  </section>
</body>
</html>
```